Window and GutterCleaning Flyer A5 size double sided.

We need a double sided A5 flyer. Side 1, is for window cleaning, side 2 is for gutter cleaning. Licensed by Borough of Marlow Council.
Phone number 0800 473 1926.
Business address 17 Fallowmere Close, North Brack Edinburgh EH31 4LP.
www.clearpane-hub-services.com
We use a LoftEye Gutter inspection Cam to view your gutters first to see if they need doing.
Window cleaning ; Professional window cleaning services, what we offer, water fed pole window cleaning able to reach windows up to 60 feet.
Conservatory cleaning.
Conservatory roof cleaning.
Fascias & Soffits cleaning.
Excellent Customer Service.
Target Market(s)
domestic houses
Industry/Entity Type
window cleaning
Look and feel
Each slider illustrates characteristics of the customer's brand and the style your logo design should communicate.

```html
<!DOCTYPE html>
<html lang="en">
<head>
<meta charset="utf-8">
<title>ClearPane Hub – Window and Gutter Cleaning Flyer</title>
<link rel="stylesheet" href="https://fonts.googleapis.com/css2?family=Montserrat:ital,wght@0,300;0,400;0,500;0,600;0,700;0,800;1,800&display=swap">
<style>
  :root {
    --bg: #d5d6d9;
    --blue: #0a57b5;
    --navy: #2b2b70;
    --ink: #1d1d1f;
    --muted: #3a3a3e;
    --white: #ffffff;
  }
  * { margin: 0; padding: 0; box-sizing: border-box; }
  html, body { width: 1200px; height: 756px; overflow: hidden; }
  body { background: var(--bg); font-family: "Montserrat", sans-serif; color: var(--ink); position: relative; }

  .flyer {
    position: absolute; top: 64px; width: 421px; height: 595px;
    background: var(--white); border-radius: 11px; overflow: hidden;
  }
  .flyer--window { left: 172px; }
  .flyer--gutter { left: 609px; }

  .hero { position: absolute; left: 0; top: 0; width: 421px; height: 296px; }
  .hero svg { display: block; }

  .brand {
    position: absolute; top: 40px; font-weight: 800; font-size: 12px;
    color: var(--navy); letter-spacing: 0.2px;
  }
  .brand::before {
    content: ""; display: inline-block; width: 9px; height: 9px;
    background: var(--navy); margin-right: 5px; vertical-align: -1px;
  }
  .flyer--window .brand { left: 42px; }
  .flyer--gutter .brand { left: 52px; }

  .headline { position: absolute; color: var(--white); font-weight: 700; letter-spacing: -0.4px; }
  .flyer--window .headline { left: 40px; top: 110px; font-size: 25.5px; line-height: 31px; }
  .flyer--gutter .headline { left: 51px; top: 104px; font-size: 29.5px; line-height: 35px; }

  .photo { position: absolute; }
  .photo--agent {
    left: 228px; top: 162px; width: 193px; height: 262px;
    background:
      radial-gradient(ellipse 45% 30% at 58% 22%, #caa07a 0%, rgba(202,160,122,0) 100%),
      radial-gradient(ellipse 55% 38% at 62% 48%, #e8c3a6 0%, rgba(232,195,166,0) 100%),
      linear-gradient(180deg, #c79b6c 0%, #dcb391 40%, #ecd9ca 70%, #f4eeea 100%);
    -webkit-mask-image: linear-gradient(90deg, transparent 0%, #000 38%);
    mask-image: linear-gradient(90deg, transparent 0%, #000 38%);
  }

  .section-title { position: absolute; left: 40px; top: 310px; color: var(--blue); }
  .section-title strong { display: block; font-weight: 700; font-size: 22.5px; line-height: 1.05; letter-spacing: -0.3px; }
  .section-title span { display: block; font-weight: 400; font-size: 16px; line-height: 1.25; }

  .body-copy {
    position: absolute; left: 40px; top: 358px; width: 190px;
    font-size: 9px; line-height: 14px; font-weight: 400;
  }
  .body-copy em { font-weight: 800; font-style: italic; }

  .checklist {
    position: absolute; left: 27px; top: 437px; list-style: none;
    font-size: 9.2px; line-height: 14px; font-weight: 300; color: var(--muted);
  }
  .checklist li svg { width: 7px; height: 7px; margin-right: 4px; vertical-align: 0; }

  .thumb { position: absolute; top: 436px; height: 73px; }
  .thumb--conservatory-roof {
    left: 191px; width: 100px;
    background: linear-gradient(150deg, #eef1f3 0%, #c7c9c4 30%, #8f8d6f 55%, #b6b9bb 80%, #d6d9dc 100%);
  }
  .thumb--conservatory {
    left: 296px; width: 101px;
    background: linear-gradient(180deg, #9a4f36 0%, #c9d7e6 18%, #f3f5f6 45%, #e9ecee 68%, #a55b41 82%, #8a9a55 100%);
  }
  .tick-badge {
    position: absolute; width: 10px; height: 10px; border-radius: 50%;
    background: var(--blue); border: 1px solid var(--white);
  }
  .tick-badge svg { position: absolute; left: 1.5px; top: 1.5px; width: 5px; height: 5px; }

  .intro { position: absolute; left: 51px; top: 318px; color: var(--blue); }
  .intro span { display: block; font-size: 14.5px; font-weight: 400; line-height: 1.25; }
  .intro strong { display: block; font-size: 15.6px; font-weight: 800; font-style: italic; line-height: 22px; letter-spacing: -0.2px; }
  .intro-copy {
    position: absolute; left: 51px; top: 381px; width: 158px;
    font-size: 10px; line-height: 15.5px;
  }
  .photo--inspection-cam {
    left: 246px; top: 302px; width: 122px; height: 139px;
    background:
      radial-gradient(ellipse 55% 35% at 45% 38%, #5a7fa4 0%, rgba(90,127,164,0) 100%),
      linear-gradient(170deg, #2c2c2e 0%, #3b3c40 55%, #c46a1d 78%, #2d2d2f 100%);
    border-radius: 6px;
    -webkit-mask-image: linear-gradient(180deg, #000 75%, transparent 100%);
    mask-image: linear-gradient(180deg, #000 75%, transparent 100%);
  }
  .strip { position: absolute; top: 442px; height: 64px; width: 108px; }
  .strip--nozzle { left: 48px; background: linear-gradient(120deg, #6f706a 0%, #9a9c95 30%, #2e45a0 55%, #cfd2d5 85%, #e4e6e8 100%); }
  .strip--roofline { left: 156px; background: linear-gradient(160deg, #3e6a2c 0%, #f2f3f4 30%, #d6d9dc 55%, #a35d42 78%, #7d4432 100%); }
  .strip--garden { left: 264px; background: linear-gradient(120deg, #5f8a3f 0%, #86ab63 40%, #6c8b55 65%, #3f4f6d 100%); }

  .footer {
    position: absolute; left: 0; bottom: 0; width: 421px; height: 76px;
    background: var(--blue); color: var(--white);
  }
  .licence { position: absolute; top: 31px; font-size: 8.3px; line-height: 12.5px; font-weight: 400; }
  .licence strong { display: block; font-weight: 700; }
  .flyer--window .licence { left: 35px; }
  .flyer--gutter .licence { left: 52px; }
  .address { position: absolute; left: 199px; top: 17px; font-size: 7.4px; line-height: 11.5px; }
  .contact { position: absolute; left: 199px; top: 46px; display: flex; align-items: center; }
  .contact .phone { font-size: 8px; font-weight: 500; margin-right: 12px; }
  .contact svg { margin-right: 4px; }
  .contact .web { font-size: 6.7px; }
</style>
</head>
<body>

<!-- Side 1: window cleaning -->
<section class="flyer flyer--window">
  <div class="hero">
    <svg width="421" height="296" viewBox="0 0 421 296">
      <defs>
        <linearGradient id="windowPhoto" x1="0" y1="0" x2="1" y2="0.6">
          <stop offset="0" stop-color="#9cb8db"/>
          <stop offset="0.35" stop-color="#e3ebf4"/>
          <stop offset="0.6" stop-color="#8aa6c8"/>
          <stop offset="0.8" stop-color="#4a6386"/>
          <stop offset="1" stop-color="#7d95b4"/>
        </linearGradient>
        <radialGradient id="windowShade" cx="0.72" cy="0.35" r="0.35">
          <stop offset="0" stop-color="#2c3f5e" stop-opacity="0.55"/>
          <stop offset="1" stop-color="#2c3f5e" stop-opacity="0"/>
        </radialGradient>
        <linearGradient id="windowWash" x1="0" y1="0" x2="1" y2="0">
          <stop offset="0" stop-color="#0a57b5" stop-opacity="0.96"/>
          <stop offset="0.5" stop-color="#0a57b5" stop-opacity="0.6"/>
          <stop offset="1" stop-color="#0a57b5" stop-opacity="0.12"/>
        </linearGradient>
      </defs>
      <g role="img" aria-label="Cleaner washing a window pane with a squeegee">
        <rect x="0" y="0" width="421" height="280" fill="url(#windowPhoto)"/>
        <rect x="0" y="0" width="421" height="280" fill="url(#windowShade)"/>
      </g>
      <rect x="0" y="0" width="421" height="280" fill="url(#windowWash)"/>
      <rect x="0" y="280" width="421" height="16" fill="var(--blue)"/>
      <path d="M0 140 C4 235 90 296 265 296 H0 Z" fill="var(--white)"/>
    </svg>
  </div>
  <div class="brand">ClearPane Hub</div>
  <h1 class="headline">Professional<br>Window<br>Cleaning</h1>

  <div class="photo photo--agent" role="img" aria-label="Smiling customer service agent wearing a headset"></div>

  <h2 class="section-title"><strong>Window</strong><span>Cleaning</span></h2>
  <p class="body-copy">We specialize in window cleaning using the latest water-fed pole technology to safely reach windows <em>up to 60 feet high.</em></p>

  <ul class="checklist">
    <li><svg viewBox="0 0 10 10"><path d="M1 5.5 L4 8.5 L9 1.5" fill="none" stroke="#0a57b5" stroke-width="1.6"/></svg>Conservatory cleaning.</li>
    <li><svg viewBox="0 0 10 10"><path d="M1 5.5 L4 8.5 L9 1.5" fill="none" stroke="#0a57b5" stroke-width="1.6"/></svg>Conservatory roof cleaning.</li>
    <li><svg viewBox="0 0 10 10"><path d="M1 5.5 L4 8.5 L9 1.5" fill="none" stroke="#0a57b5" stroke-width="1.6"/></svg>Fascias &amp; Soffits cleaning.</li>
    <li><svg viewBox="0 0 10 10"><path d="M1 5.5 L4 8.5 L9 1.5" fill="none" stroke="#0a57b5" stroke-width="1.6"/></svg>Excellent Customer Service.</li>
  </ul>

  <div class="thumb thumb--conservatory-roof" role="img" aria-label="Conservatory roof panels before cleaning"></div>
  <div class="thumb thumb--conservatory" role="img" aria-label="Clean white conservatory on a brick house"></div>
  <span class="tick-badge" style="left:186px; top:431px;"><svg viewBox="0 0 10 10"><path d="M1 5.5 L4 8.5 L9 1.5" fill="none" stroke="#fff" stroke-width="2"/></svg></span>
  <span class="tick-badge" style="left:291px; top:431px;"><svg viewBox="0 0 10 10"><path d="M1 5.5 L4 8.5 L9 1.5" fill="none" stroke="#fff" stroke-width="2"/></svg></span>

  <footer class="footer">
    <p class="licence">Licensed by<strong>Borough of Marlow Council</strong></p>
    <p class="address">17 Fallowmere Close, North Brack,<br>Edinburgh EH31 4LP</p>
    <p class="contact">
      <svg width="8" height="8" viewBox="0 0 10 10"><path d="M2 0.5 L4 2.5 L3 4 C3.8 5.6 4.6 6.4 6 7 L7.5 6 L9.5 8 L8.3 9.5 C4 9.3 0.7 6 0.5 1.7 Z" fill="#fff"/></svg>
      <span class="phone">0800 473 1926</span>
      <svg width="7" height="7" viewBox="0 0 10 10"><circle cx="5" cy="5" r="4.3" fill="none" stroke="#fff" stroke-width="0.9"/><ellipse cx="5" cy="5" rx="2" ry="4.3" fill="none" stroke="#fff" stroke-width="0.9"/><path d="M0.7 5 H9.3" stroke="#fff" stroke-width="0.9"/></svg>
      <span class="web">www.clearpane-hub-services.com</span>
    </p>
  </footer>
</section>

<!-- Side 2: gutter cleaning -->
<section class="flyer flyer--gutter">
  <div class="hero">
    <svg width="421" height="296" viewBox="0 0 421 296">
      <defs>
        <linearGradient id="gutterPhoto" x1="0" y1="0" x2="1" y2="0.8">
          <stop offset="0" stop-color="#6d8f52"/>
          <stop offset="0.35" stop-color="#7fa262"/>
          <stop offset="0.6" stop-color="#3e4a55"/>
          <stop offset="0.8" stop-color="#6d7886"/>
          <stop offset="1" stop-color="#8d96a2"/>
        </linearGradient>
        <radialGradient id="gutterShade" cx="0.78" cy="0.3" r="0.3">
          <stop offset="0" stop-color="#1c1f26" stop-opacity="0.6"/>
          <stop offset="1" stop-color="#1c1f26" stop-opacity="0"/>
        </radialGradient>
        <linearGradient id="gutterWash" x1="0" y1="0" x2="1" y2="0">
          <stop offset="0" stop-color="#0a57b5" stop-opacity="0.96"/>
          <stop offset="0.5" stop-color="#0a57b5" stop-opacity="0.55"/>
          <stop offset="1" stop-color="#0a57b5" stop-opacity="0.08"/>
        </linearGradient>
      </defs>
      <g role="img" aria-label="Carbon gutter vacuum pole with camera over a house gutter">
        <rect x="0" y="0" width="421" height="280" fill="url(#gutterPhoto)"/>
        <rect x="0" y="0" width="421" height="280" fill="url(#gutterShade)"/>
      </g>
      <rect x="0" y="0" width="421" height="280" fill="url(#gutterWash)"/>
      <rect x="0" y="280" width="421" height="16" fill="var(--blue)"/>
      <path d="M0 140 C4 235 90 296 265 296 H0 Z" fill="var(--white)"/>
    </svg>
  </div>
  <div class="brand">ClearPane Hub</div>
  <h1 class="headline">Gutter<br>Cleaning</h1>

  <div class="intro">
    <span>We use</span>
    <strong>a LoftEye Gutter<br>inspection Cam</strong>
  </div>
  <p class="intro-copy">to view your gutters first to see if they need doing.</p>

  <div class="photo photo--inspection-cam" role="img" aria-label="Handheld gutter inspection camera monitor on a pole"></div>

  <div class="strip strip--nozzle" role="img" aria-label="Vacuum nozzle inside a dirty gutter"></div>
  <div class="strip strip--roofline" role="img" aria-label="Roofline showing gutter, fascia and soffit"></div>
  <div class="strip strip--garden" role="img" aria-label="Gutter vacuum pole working over a garden"></div>
  <span class="tick-badge" style="left:43px; top:437px;"><svg viewBox="0 0 10 10"><path d="M1 5.5 L4 8.5 L9 1.5" fill="none" stroke="#fff" stroke-width="2"/></svg></span>
  <span class="tick-badge" style="left:151px; top:437px;"><svg viewBox="0 0 10 10"><path d="M1 5.5 L4 8.5 L9 1.5" fill="none" stroke="#fff" stroke-width="2"/></svg></span>
  <span class="tick-badge" style="left:259px; top:437px;"><svg viewBox="0 0 10 10"><path d="M1 5.5 L4 8.5 L9 1.5" fill="none" stroke="#fff" stroke-width="2"/></svg></span>

  <footer class="footer">
    <p class="licence">Licensed by<strong>Borough of Marlow Council</strong></p>
    <p class="address">17 Fallowmere Close, North Brack,<br>Edinburgh EH31 4LP</p>
    <p class="contact">
      <svg width="8" height="8" viewBox="0 0 10 10"><path d="M2 0.5 L4 2.5 L3 4 C3.8 5.6 4.6 6.4 6 7 L7.5 6 L9.5 8 L8.3 9.5 C4 9.3 0.7 6 0.5 1.7 Z" fill="#fff"/></svg>
      <span class="phone">0800 473 1926</span>
      <svg width="7" height="7" viewBox="0 0 10 10"><circle cx="5" cy="5" r="4.3" fill="none" stroke="#fff" stroke-width="0.9"/><ellipse cx="5" cy="5" rx="2" ry="4.3" fill="none" stroke="#fff" stroke-width="0.9"/><path d="M0.7 5 H9.3" stroke="#fff" stroke-width="0.9"/></svg>
      <span class="web">www.clearpane-hub-services.com</span>
    </p>
  </footer>
</section>

</body>
</html>
```